New B2C website design to help dads be better dads

DadHarbor is a website to help dads be the “best dad you can be.”

We require our website to be designed into a PSD format, no coding necessary.

The general concept is a two-page design. The first page is the login page, the second page is the home page. Once at the home page, rather than navigating to and from different pages, the user will push and pull through different visual and functional layers of the hierarchy. In theory, this should add to the user experience by having a visual anchor of where they are (through layered pagination) as well as improving loading times since the new information should only be a delta in data load versus a brand new page load.

The general look-and-feel we are going for is clean, simple, minimal. This means that the winning design will show us a good eye for web-optimized typography, good use of white (negative) space, and good use of a visually pleasing grid.

We require a total of 6 page "views" plus the landing page. We note that many of the views are similar to one another.
Landing page
Milestone view
Task view
Content view, articles
Content view, products
Search view
What's new view

Please review all of the additional information provided as well as the attachments for examples.

We provide the following websites as good references for:

Typography:
http://example-kelvorn.com/journal/

Use of white space:
http://www.trenvaskit.com/
http://moldrefin.com/

Example for “scrolling” page concept as well as good balance of color, typography, and white space:
http://www.qorbitalmeet.eu/

Please contact us with questions so that we can guide your design effort.
Updates

Hello designers,

The following information is added to help guide the design process:

1.  For the text dialogue below the landing page, please assume the following word count:
"why are we making dad harbor?": 250 words
"who are we?" 200 words
"what's the deal with the penguin logo?" 300 words

For the social media links, please see http://www.gravelplumbs.com/
Notice the floating "social" bar that is always to the right.  This is the concept we are going for, please try to implement this as you see fit. 

Target Market(s)

Fathers of young children ages 0-6 years old.

Industry/Entity Type

Product

Font styles to use
Sans Serif

Requirements
Must have
• Clean lines, minimal design concept

Incorporation of our logo (see attached document)

Header content is static for all views after landing page, see example

This page WILL be responsive, please keep that in mind when designing
The timeline bar should be to the left, with the timeline bar’s “milestones” also being responsive.

Designer is free to suggest font types, but any fonts used must be royalty-free and web-optimized. We request a minimum number of font types as well as fonts that load relatively fast. We reinforce that visually appealing typography is a significant factor in the winning design choice.

While we are not expecting the winning design to include code, please keep in mind that the final implementation needs to be optimized for desktop, tablet, and mobile platforms.

If you are using stock photography that is not generated by you, please provide where/how we can obtain imagery, as well as price.

All custom graphics must be available in original formats; Photoshop/GIMP layered files for layout design, and vector formats for logos, icons and other graphical elements.

Please incorporate “Blue” into design elements as you see fit, as the RGB 67 74 169 Blue is the primary color used in our brand. The complement to this blue is 255 202 0, a brownish orange. Feel free to use this color as well, although please keep it to a lesser amount.

Background color is your choice, do not feel the need to use the grey.
Should not have
• Excessive graphical content such that it affects loading times

Excessive use of too many font types such that it affects loading times

```html
<!DOCTYPE html>
<html lang="en">
<head>
<meta charset="utf-8">
<title>DadHarbor – Prepare for the baby arrival</title>
<link rel="stylesheet" href="https://fonts.googleapis.com/css2?family=Noto+Sans:wght@400;700&family=Squada+One&display=swap">
<style>
  :root{
    --navy:#1f2d6e;
    --brand-blue:#434aa9;
    --orange:#f39a1c;
    --orange-line:#f5a81c;
    --panel:#e6e6e6;
    --line:#c8c8c8;
    --text:#3a3a3a;
    --muted:#555;
    --white:#fff;
    --star-on:#f5b820;
    --star-off:#bdbdbd;
    --share-bg:#f4efe4;
  }
  *{box-sizing:border-box;margin:0;padding:0}
  html,body{width:1200px;height:1001px;overflow:hidden;background:var(--white)}
  body{position:relative;font-family:"Noto Sans",Arial,sans-serif;color:var(--text)}
  .abs{position:absolute}

  /* header */
  .site-header{left:0;top:0;width:1200px;height:138px;background:linear-gradient(#fff 0%,#fafafa 45%,#e4e4e4 100%);border-bottom:4px solid var(--orange-line)}
  .brand{left:30px;top:30px;width:120px;text-align:center}
  .brand-mark{width:46px;height:46px;border-radius:50%;background:var(--navy);margin:0 auto 14px}
  .brand-name{font-size:15px;font-weight:700;color:var(--navy);letter-spacing:.5px}
  .welcome{left:192px;top:14px;font-family:"Squada One",Arial,sans-serif;font-size:40px;color:#111;letter-spacing:.3px}
  .score{left:193px;top:86px;font-size:16px;color:#222}
  .score b{color:var(--navy)}
  .search-field{left:438px;top:77px;width:300px;height:43px;background:#fff;border:1px solid #d4d4d4;border-radius:4px}
  .btn{background:var(--navy);color:#fff;font-weight:700;font-size:17px;letter-spacing:.5px;display:flex;align-items:center;justify-content:center;border-radius:3px}
  .btn-search{left:748px;top:77px;width:114px;height:43px}
  .account{left:959px;top:87px;font-size:16px;color:#222}
  .btn-logout{left:1058px;top:78px;width:114px;height:42px}

  /* timeline */
  .timeline{left:91px;top:142px;width:2px;height:859px;background:var(--line)}
  .milestone-flag{left:22px;top:202px;width:56px;height:38px;background:var(--orange);color:#fff;text-align:center;font-size:13px;line-height:14px;padding-top:4px;clip-path:polygon(0 0,100% 0,82% 50%,100% 100%,0 100%)}
  .milestone-flag b{font-size:19px;font-weight:400;display:block;line-height:18px}
  .flag-pole{left:22px;top:240px;width:4px;height:46px;background:var(--orange)}

  .milestone-panel{left:110px;top:192px;width:1062px;height:770px;background:var(--panel);border-radius:10px}
  .collapse{left:77px;top:207px;width:31px;height:31px;border-radius:50%;background:#fff;border:2px solid #333}
  .collapse::after{content:"";position:absolute;left:7px;top:12px;width:13px;height:3px;background:#333}
  .milestone-title{left:114px;top:209px;font-size:20px;color:#222}

  .task-list{left:132px;top:274px;width:263px;height:288px;background:#fff;border:1px solid #cfcfcf;list-style:none;padding:16px 0 0 20px}
  .task-list li{display:flex;align-items:center;height:32.8px;font-size:17px;color:#333}
  .check{width:20px;height:20px;border:1px solid #c9c9c9;border-radius:3px;background:#f1f1f1;margin-right:15px;display:flex;align-items:center;justify-content:center}
  .check.done{background:#dbe6f7;border-color:#7a95c9}

  .rate{left:156px;top:580px;font-size:15px;color:#222;display:flex;align-items:center;gap:14px}
  .stars{display:flex;gap:2px}
  .comments-label{left:156px;top:617px;font-size:15px;color:#222}
  .comment-text{left:156px;top:644px;width:226px;font-size:15px;line-height:20px;color:#333}

  /* article */
  .article-title{left:424px;top:210px;font-size:29px;color:#222}
  .likes{left:917px;top:216px;display:flex;align-items:center;gap:14px;font-size:15px;color:#333}
  .likes b{color:var(--navy)}
  .article{left:409px;top:271px;width:711px;height:665px;background:#fff}
  .article p,.article .review{position:absolute;left:24px;width:668px;font-size:15px;line-height:20.5px;color:#333}
  .intro{top:22px}
  .article-photo{position:absolute;left:235px;top:129px;width:242px;height:144px;background:linear-gradient(135deg,#3a3430 0%,#8a7868 45%,#c7a98d 75%,#5b4b40 100%)}
  .body-copy{top:294px;left:29px!important}
  .reviews-head{position:absolute;left:29px;top:418px;font-size:15px;color:var(--navy)}
  .review{left:29px!important}
  .review strong{font-weight:400;color:#111;display:block}
  .helpful{display:block;margin-top:8px;color:#333}
  .helpful span{color:var(--navy)}
  .r1{top:446px}
  .r2{top:548px}

  .more{left:580px;top:942px;width:40px;height:40px;border-radius:50%;background:var(--brand-blue);border:2px solid #fff}

  /* share bar */
  .share-bar{left:1140px;top:214px;width:64px;height:258px;background:var(--share-bg);border:1px solid #b9b2a2;border-radius:6px 0 0 6px}
  .share-label{position:absolute;left:0;top:9px;width:60px;text-align:center;font-size:15px;color:#222}
  .share-dot{position:absolute;left:10px;width:48px;height:48px;border-radius:50%;background:var(--brand-blue);border:2px solid #fff}
</style>
</head>
<body>
  <header class="site-header abs">
    <div class="brand abs"><div class="brand-mark"></div><div class="brand-name">DADHARBOR</div></div>
    <h1 class="welcome abs">Welcome Owen, what would you like to do today?</h1>
    <div class="score abs">Super Dad Score: <b>10,500</b></div>
    <div class="search-field abs"></div>
    <div class="btn btn-search abs">SEARCH</div>
    <div class="account abs">My account</div>
    <div class="btn btn-logout abs">LOGOUT</div>
  </header>

  <div class="timeline abs"></div>
  <div class="milestone-panel abs"></div>
  <div class="flag-pole abs"></div>
  <div class="milestone-flag abs"><b>1</b>mo</div>
  <div class="collapse abs"></div>
  <h2 class="milestone-title abs" style="font-weight:400">Prepare for the baby arrival</h2>

  <ul class="task-list abs">
    <li><span class="check"></span>Buy a crib</li>
    <li><span class="check"></span>As semble the crib</li>
    <li><span class="check"></span>Buy a stroller</li>
    <li><span class="check done"><svg width="14" height="12" viewBox="0 0 14 12"><path d="M1 6l4 4 8-9" fill="none" stroke="#2a55b8" stroke-width="2.4"/></svg></span>Buy a carseat</li>
    <li><span class="check"></span>Install a carseat</li>
    <li><span class="check"></span>Learn to change a diaper</li>
    <li><span class="check"></span>Learn to hold a baby</li>
    <li><span class="check"></span>Set a feeding schedule</li>
  </ul>

  <div class="rate abs">Rate this :
    <svg class="stars" width="104" height="20" viewBox="0 0 104 20">
      <defs><path id="star" d="M10 1l2.6 5.6 6 .7-4.5 4.1 1.2 6L10 14.4 4.7 17.4l1.2-6L1.4 7.3l6-.7z"/></defs>
      <use href="#star" fill="var(--star-on)"/><use href="#star" x="20" fill="var(--star-on)"/><use href="#star" x="40" fill="var(--star-on)"/><use href="#star" x="60" fill="var(--star-off)"/><use href="#star" x="80" fill="var(--star-off)"/>
    </svg>
  </div>
  <div class="comments-label abs">Comments:</div>
  <p class="comment-text abs">Lorem ipsum dolor sit amet, consectetur adipisicing elit, sed do eiusmod tempor incididunt ut labore et dolore magna aliqua. Ut enim ad minim veniam.</p>

  <h2 class="article-title abs" style="font-weight:400">Just Call Me Dr. Car Seat</h2>
  <div class="likes abs">
    <svg width="106" height="20" viewBox="0 0 104 20">
      <use href="#star" fill="var(--star-on)"/><use href="#star" x="20" fill="var(--star-on)"/><use href="#star" x="40" fill="var(--star-on)"/><use href="#star" x="60" fill="var(--star-off)"/><use href="#star" x="80" fill="var(--star-off)"/>
    </svg>
    <span><b>3,121</b> likes</span>
  </div>

  <article class="article abs">
    <p class="intro">I went out to buy my first car seat and had to earn my PhD in car seats, Newtonian physics, and anti-stain technology. Lorem ipsum dolor sit amet, consectetur adipisicing elit, sed do eiusmod tempor incididunt ut labore et dolore magna aliqua. Ut enim ad minim veniam, quis nostrud exercitation ullamco laboris nisi ut aliquip ex ea commodo consequat.</p>
    <div class="article-photo" role="img" aria-label="Photo of a father buckling his baby into a car seat"></div>
    <p class="body-copy">Lorem ipsum dolor sit amet, consectetur adipisicing elit, sed do eiusmod tempor incididunt ut labore et dolore magna aliqua. Ut enim ad minim veniam, quis nostrud exercitation ullamco laboris nisi ut aliquip ex ea commodo consequat. Duis aute irure dolor in reprehenderit in voluptate velit esse cillum dolore eu fugiat nulla pariatur. Excepteur sint occaecat cupidatat non proident, sunt in culpa qui officia deserunt mollit anim id est laborum.</p>
    <div class="reviews-head">Follow Dad’s Reviews:</div>
    <div class="review r1"><strong>DadSierra204:</strong>Lorem ipsum dolor sit amet, consectetur adipisicing elit, sed do eiusmod tempor incididunt ut labore et dolore magna aliqua.<span class="helpful"><span>152</span> other Dad’s found this review helpful.</span></div>
    <div class="review r2"><strong>DadSierra204:</strong>Lorem ipsum dolor sit amet, consectetur adipisicing elit, sed do eiusmod tempor incididunt ut labore et dolore magna aliqua.<span class="helpful"><span>105</span> other Dad’s found this review helpful.</span></div>
  </article>

  <div class="more abs">
    <svg width="36" height="36" viewBox="0 0 36 36"><path d="M11 12l7 6 7-6M11 19l7 6 7-6" fill="none" stroke="#fff" stroke-width="2.4"/></svg>
  </div>

  <aside class="share-bar abs">
    <div class="share-label">Share</div>
    <div class="share-dot" style="top:31px"></div>
    <div class="share-dot" style="top:86px"></div>
    <div class="share-dot" style="top:140px"></div>
    <div class="share-dot" style="top:195px"></div>
  </aside>
</body>
</html>
```